Computer consultant business card

Bexil Software is a newly started computer consulting company. It's a small one-man company that provides mostly Vornix applications but also websites in collaboration with designers. I'm running this company on the side of full time university studies.

I want the final design to be clean and memorable. Be creative! :)

Some inspiration:
http://www.pixelmarta.com/design/48317
http://www.pixelmarta.com/design/2739164/business-card-design-by-frostlynk
http://www.pixelmarta.com/design/604281/business-card-design-by-koralind-vestrabanu

See attachment for my company logo.
Updates

I would like to thank everyone for submitting! I'll need a couple of days to review and ultimately select a design.

Target Market(s)

Non-technical entrepreneurs and small companies.

Industry/Entity Type

University

Requirements
Must have
• My company logo.
In any way, both colors from my logo.
First- and last name, e-mail and phone number.
Double-sided design.
Nice to have
• Something creative with the symbol in my logo

```html
<!DOCTYPE html>
<html lang="en">
<head>
<meta charset="utf-8">
<title>Bexil Software — Business Card</title>
<link rel="stylesheet" href="https://fonts.googleapis.com/css2?family=Open+Sans:wght@400;600;800&display=swap">
<style>
  :root {
    --backdrop: #e4e4e4;
    --brand-blue: #3f6db5;
    --brand-blue-deep: #2f5a9c;
    --brand-blue-light: #4a78c0;
    --charcoal: #2f2d2e;
    --paper: #ffffff;
    --ink: #2b2b2b;
  }
  * { box-sizing: border-box; margin: 0; padding: 0; }
  html, body { width: 1200px; height: 1016px; overflow: hidden; }
  body {
    background: var(--backdrop);
    font-family: "Open Sans", Arial, sans-serif;
    position: relative;
  }
  .card {
    position: absolute;
    left: 250px;
    width: 700px;
    height: 400px;
    border-radius: 22px;
    overflow: hidden;
    box-shadow: 0 10px 28px rgba(0,0,0,0.22);
  }
  .card--back {
    top: 80px;
    background: radial-gradient(circle at 50% 50%, var(--brand-blue-light) 0%, var(--brand-blue) 45%, var(--brand-blue-deep) 100%);
  }
  .card--front { top: 536px; background: var(--paper); }
  .card-art { position: absolute; inset: 0; width: 100%; height: 100%; }

  .wordmark {
    position: absolute;
    display: flex;
    align-items: center;
    gap: 16px;
    font-weight: 600;
    letter-spacing: 1px;
    line-height: 1;
    white-space: nowrap;
  }
  .wordmark-dot { border-radius: 50%; flex: none; }
  .card--back .wordmark {
    left: 50%; top: 50%;
    transform: translate(-50%, -50%);
    color: var(--paper);
    font-size: 84px;
  }
  .card--back .wordmark-dot { width: 70px; height: 70px; background: var(--paper); }
  .card--front .wordmark {
    left: 425px; top: 92px;
    color: var(--ink);
    font-size: 62px;
  }
  .card--front .wordmark-dot { width: 52px; height: 52px; background: var(--brand-blue); }

  .identity { position: absolute; left: 30px; top: 176px; }
  .identity-name {
    color: var(--brand-blue);
    font-weight: 800;
    font-size: 30px;
    letter-spacing: 0.5px;
  }
  .identity-title {
    color: var(--paper);
    font-size: 19px;
    margin-left: 112px;
    margin-top: -4px;
  }

  .contact {
    position: absolute;
    display: flex;
    align-items: center;
    gap: 8px;
    color: var(--ink);
    font-size: 18px;
    white-space: nowrap;
  }
  .contact--phone { left: 262px; top: 336px; }
  .contact--email { right: 34px; top: 270px; }
  .contact-icon { width: 24px; height: 24px; flex: none; }
</style>
</head>
<body>

  <section class="card card--back" aria-label="Card back">
    <div class="wordmark"><span class="wordmark-dot"></span>bexil</div>
  </section>

  <section class="card card--front" aria-label="Card front">
    <svg class="card-art" viewBox="0 0 700 400" aria-hidden="true">
      <path d="M0,0 H556 C380,70 214,230 190,400 H0 Z" fill="var(--brand-blue)"/>
      <path d="M0,0 H528 C356,70 196,230 176,400 H0 Z" fill="var(--paper)"/>
      <path d="M0,0 H512 C340,70 182,230 162,400 H0 Z" fill="var(--charcoal)"/>
    </svg>

    <div class="identity">
      <p class="identity-name">YOUR NAME</p>
      <p class="identity-title">Job Title</p>
    </div>

    <div class="wordmark"><span class="wordmark-dot"></span>bexil</div>

    <p class="contact contact--email">
      <svg class="contact-icon" viewBox="0 0 24 24" aria-hidden="true">
        <circle cx="12" cy="12" r="10.5" fill="none" stroke="var(--brand-blue)" stroke-width="1.8"/>
        <rect x="6.5" y="8" width="11" height="8" fill="var(--brand-blue)"/>
        <path d="M6.5,8 L12,12.5 L17.5,8" fill="none" stroke="var(--paper)" stroke-width="1"/>
      </svg>
      name@domainname.com
    </p>

    <p class="contact contact--phone">
      <svg class="contact-icon" viewBox="0 0 24 24" aria-hidden="true">
        <circle cx="12" cy="12" r="10.5" fill="none" stroke="var(--brand-blue)" stroke-width="1.8"/>
        <rect x="8.5" y="6" width="7" height="12" rx="1.5" fill="none" stroke="var(--brand-blue)" stroke-width="1.6"/>
      </svg>
      000-000-000
    </p>
  </section>

</body>
</html>
```